Accountant website

Please design a accountant website for www.fenwaybridgeadvisory.com.au. This site is majorly out of date, and is not supported by modern browsers.

The style should use the reds from the design at dev.fenwaybridgeadvisory.com.au, and should be modern and make use of Slides (large content slides that the user scrolls through on the front page).

The content is largely already on the site, however happy to move some around to suit the modern design as required.

The dev.fenwaybridgeadvisory.com.au was a rough mock up that I have completed that the client is "happy" with the direction, however this needs a lot of polish and finishing touches, and I will accept designs that differ from this, but highly recommend that this is used as a guide.

Ready to be sliced PSD Only - HTML no required.

In all honesty, although I can technically do a lot of this, the polished finished I want for this site has eluded me in a few attempts, and therefore I am looking out there at you much more artistic people to finish (or redesign if required) this site.

Target Market(s)

Higher end Small - Medium Business

Industry/Entity Type

Accountant

Requirements
Must have
• Must use the logo from dev.fenwaybridgeadvisory.com.au use exactly the red colours as defined in this layout. A basic layout PSD (to get the colour etc) and the logo in ai format is attached to this project. Please ignore the SSL warning on the development site.

The final product does NOT have to be the same as shown on dev.fenwaybridgeadvisory.com.au however the red colour scheme must be used. The client DOES want the logo on the RIGHT.

Must have a front landing page design, and a page layout that considers the other page content (at least one separate PSD)
Nice to have
• I really am looking at a slide format for the front page simular to:

http://www.quillo.com/au/
http://www.vaultmoor.com/

The attached photos should be used on the site. Was considering a rotating banner with these images are a watermark background on a solid Red header bar, but happy to be shown other options.
Should not have
• Please no "Layout Goblin" submissions.

```html
<!DOCTYPE html>
<html lang="en">
<head>
<meta charset="utf-8">
<title>Fenway Bridge Advisory</title>
<link rel="stylesheet" href="https://fonts.googleapis.com/css2?family=Source+Sans+3:wght@400;600;700&family=Oswald:wght@500&display=swap">
<style>
:root{
  --red:#a3302f;
  --red-bright:#b22a2a;
  --ink:#3a3a3a;
  --muted:#666;
  --white:#fff;
  --topbar:#4a4a4a;
  --grey-band:#eeeeee;
  --footer:#3d3d3d;
  --footer-bottom:#262626;
}
*{box-sizing:border-box;margin:0;padding:0}
html,body{width:741px;height:1200px;overflow:hidden}
body{position:relative;font-family:"Source Sans 3",sans-serif;color:var(--ink);background:var(--white)}
.abs{position:absolute}
.topbar{left:0;top:0;width:741px;height:30px;background:var(--topbar)}
.topbar .login{left:54px;top:8px;color:var(--white);font-size:11px;letter-spacing:.2px}
.header{left:0;top:30px;width:741px;height:71px;background:var(--white)}
.nav{left:54px;top:30px;display:flex;gap:0;font-size:11.5px}
.nav a{position:absolute;top:0;color:var(--ink);text-decoration:none;white-space:nowrap}
.nav a.active{color:var(--red-bright)}
.brand{left:534px;top:42px;color:#1c1c1c;font-weight:700;line-height:1}
.brand .name{font-size:22px;letter-spacing:-.3px}
.brand .sub{font-size:10.5px;margin-top:3px;letter-spacing:.2px}
.hero{left:0;top:101px;width:741px;height:311px;background:linear-gradient(90deg,#9aa7b3 0%,#b9c2c9 40%,#a0958d 70%,#7d8a7e 100%)}
.hero-caption{left:54px;top:310px;width:282px;height:84px;background:rgba(45,45,45,.82);padding:10px 14px}
.hero-caption h1{font-family:"Oswald",sans-serif;font-weight:500;font-size:19px;color:var(--white);letter-spacing:.2px;line-height:1.1}
.hero-caption p{font-size:9.4px;color:#eee;line-height:1.6;margin-top:8px}
.dots{left:655px;top:397px;display:flex;gap:3px}
.dots span{width:6px;height:6px;border-radius:50%;background:#333}
.dots span.on{background:var(--white);border:1px solid #333}
.intro{left:0;top:412px;width:741px;height:264px;background:var(--red);color:var(--white);text-align:center}
.intro h2{position:absolute;left:0;top:20px;width:741px;font-size:17px;font-weight:600}
.intro .lead{position:absolute;left:54px;top:52px;width:634px;font-size:8.2px;line-height:1.65}
.svc{position:absolute;top:108px;width:170px;text-align:center}
.svc svg{display:block;margin:0 auto;height:54px}
.svc h3{font-size:12.5px;font-weight:600;margin-top:16px}
.svc p{font-size:8.5px;line-height:1.6;margin-top:4px;letter-spacing:.2px}
.welcome{left:83px;top:700px;width:404px}
.title{font-size:16px;font-weight:400;color:#444}
.title em{font-style:normal;color:var(--red-bright)}
.subtitle{font-size:11px;color:#444;margin-top:6px}
.body-copy{font-size:7.8px;line-height:1.72;color:var(--muted);margin-top:8px}
.clients{left:513px;top:704px}
.clients h2{font-size:13.5px;font-weight:400;color:#444}
.faces{display:grid;grid-template-columns:repeat(3,47px);gap:5px;margin-top:10px}
.faces div{height:45px;background:linear-gradient(160deg,#c9b3a1,#6d5a4d)}
.grey-band{left:0;top:856px;width:741px;height:193px;background:var(--grey-band)}
.person{left:100px;top:864px;width:118px;height:185px;background:linear-gradient(180deg,#d9d9d9,#8f8f8f);border-radius:50px 50px 0 0}
.difference{left:263px;top:880px;width:402px}
.difference .title{font-size:17px;color:var(--red-bright)}
.footer{left:0;top:1049px;width:741px;height:115px;background:var(--footer)}
.fcol{position:absolute;top:1065px;color:var(--white)}
.fcol h4{font-size:11px;font-weight:400;margin-bottom:6px}
.fcol li{list-style:none;font-size:8.2px;line-height:17.6px;color:#eee}
.badge{left:592px;top:1089px;width:95px;height:40px;background:#5a5a5a;border:1px solid #777}
.bottom{left:0;top:1164px;width:741px;height:36px;background:var(--footer-bottom)}
.copy{left:54px;top:1177px;font-size:8.5px;color:#ddd}
.social{left:577px;top:1173px;display:flex;gap:10px}
.social span{width:19px;height:19px;border-radius:50%}
</style>
</head>
<body>
<div class="abs topbar"><span class="abs login">CLIENT LOGIN</span></div>
<div class="abs header"></div>
<nav class="abs nav" style="top:61px">
  <a class="active" style="left:0">HOME</a>
  <a style="left:52px">ABOUT</a>
  <a style="left:109px">SERVICES</a>
  <a style="left:176px">CONTACT</a>
  <a style="left:245px">TESTIMONIALS</a>
  <a style="left:338px">NEWS</a>
</nav>
<div class="abs brand"><div class="name">FENWAY BRIDGE</div><div class="sub">ADVISORY</div></div>

<div class="abs hero" role="img" aria-label="Smiling businesswoman in a red top seated at a marina with sailing boats behind"></div>
<div class="abs hero-caption">
  <h1>THE DAYS OF BUYING EXPENSIVE</h1>
  <p>Jerta baditaut onsequser untur magni dolores eoquie volup tate msequi nesciunt. Voluptatem accusantium dolorem.</p>
</div>
<div class="abs dots"><span class="on"></span><span></span><span></span><span></span></div>

<section class="abs intro">
  <h2>Getting to Know Fenway Bridge Advisory</h2>
  <p class="lead">Vivamus sagittis lacus vel augue laoreet rutrum faucibus dolor auctor. Aenean lacinia bibendum nulla sed consectetur. Because we think it's time for a new exciting challeng e! Are you ready for an adventure to remember for a lifetime? Accusantium quam, ultricies eget tempor id, aliquam eget nibh et. Maecen aliquam, risus at sempe</p>
  <div class="svc" style="left:91px">
    <svg viewBox="0 0 54 54" fill="none" stroke="#fff" stroke-width="2.6"><path d="M4 2h26l10 10v10M4 2v50h22"/><path d="M30 2v10h10"/><path d="M10 18h20M10 26h20M10 34h14M10 42h12"/><circle cx="40" cy="40" r="11"/><path d="M40 36v12M40 31v2"/></svg>
    <h3>Business Establishment</h3>
    <p>Lorem ipsum dolor sit amet adipis msan. Morbi ut elit utipsum tristiquea Pellentesque habitant morbi.</p>
  </div>
  <div class="svc" style="left:283px">
    <svg viewBox="0 0 54 54" fill="none" stroke="#fff" stroke-width="2.6" stroke-linejoin="round"><path d="M52 2L2 32l16 6 8 14 4-12 12 6z"/><path d="M52 2L18 38M52 2L30 40"/></svg>
    <h3>Business Cessation</h3>
    <p>Lorem ipsum dolor sit amet adipis msan. Morbi ut elit utipsum tristiquea Pellentesque habitant morbi.</p>
  </div>
  <div class="svc" style="left:479px">
    <svg viewBox="0 0 54 54" fill="#fff"><path d="M27 1c-10 0-17 7-17 16 0 8 6 12 8 20h18c2-8 8-12 8-20 0-9-7-16-17-16z"/><rect x="18" y="40" width="18" height="3" rx="1"/><rect x="18" y="45" width="18" height="3" rx="1"/><rect x="21" y="50" width="12" height="3" rx="1"/></svg>
    <h3>Business Services</h3>
    <p>Lorem ipsum dolor sit amet adipis msan. Morbi ut elit utipsum tristiquea Pellentesque habitant morbi.</p>
  </div>
</section>

<section class="abs welcome">
  <h2 class="title">Welcome to <em>Fenway Bridge</em></h2>
  <p class="subtitle">Doloremque laudantium totames</p>
  <p class="body-copy">Pellentesque habitant morbi tristique senectus et netus et malesuada fames ac turpis egestas. Lorem ipiisum dolor sit amet, consectetur adipiscing elit. Nunc id lobortis diam, vel lobortis ipsum.At vero eos et accusamiu s et iusto odio dignissimos ducimus qui blanditiis praesentium voluptatu deleniti atque corrupti quos dolore s et quas molestias excep turi sint occaecati cupiditate non provident similique Lorem ipsum dolor sit amet, c onsectetur adipisicing elitsed dore eiusmod tempor incididunt ut labore etman dolore magna aliqua nimad minim veniam pulsar adiya</p>
</section>
<aside class="abs clients">
  <h2>View wht our client says</h2>
  <div class="faces">
    <div role="img" aria-label="Client portrait"></div>
    <div role="img" aria-label="Client portrait"></div>
    <div role="img" aria-label="Client portrait"></div>
    <div role="img" aria-label="Client portrait"></div>
    <div role="img" aria-label="Client portrait"></div>
    <div role="img" aria-label="Client portrait"></div>
  </div>
</aside>

<div class="abs grey-band"></div>
<div class="abs person" role="img" aria-label="Businesswoman in a grey suit standing with arms crossed"></div>
<section class="abs difference">
  <h2 class="title">Fenway Bridge Advisory Difference</h2>
  <p class="subtitle">Doloremque laudantium totames</p>
  <p class="body-copy">Pellentesque habitant morbi tristique senectus et netus et malesuada fames ac turpis egestas. Lorem ipiisum dolor sit amet, consectetur adipiscing elit. Nunc id lobortis diam, vel lobortis ipsum.At vero eos et accusamiu s et iusto odio dignissimos ducimus qui blanditiis praesentium voluptatu deleniti atque corrupti quos dolore s et quas molestias excep turi sint occaecati cupiditate non provident similique Lorem ipsum dolor sit amet, c onsectetur adipisicing elitsed dore eiusmod tempor incididunt ut labore etman dolore magna aliqua nimad minim veniam pulsar adiya</p>
</section>

<footer class="abs footer"></footer>
<div class="fcol" style="left:54px"><h4>US States</h4><ul><li>Team Portal</li><li>FeedbacK Exchange</li><li>Proin sit amet nulla</li><li>Consectetur adipiscing</li></ul></div>
<div class="fcol" style="left:190px"><h4>Who We Are</h4><ul><li>Pagewright</li><li>Searchly</li><li>Clipstream</li><li>Lenspage</li></ul></div>
<div class="fcol" style="left:310px"><h4>Outreach</h4><ul><li>Web Design Tauranga</li><li>Web Design Papamoa</li><li>Web Design Te Puke</li><li>Web Design Mt Maunganui</li></ul></div>
<div class="fcol" style="left:458px"><h4>Business Consulting</h4><ul><li>Web Design Tauranga</li><li>Web Design Papamoa</li><li>Web Design Te Puke</li><li>Web Design Mt Maunganui</li></ul></div>
<div class="abs badge" role="img" aria-label="Professional accreditation badge"></div>

<div class="abs bottom"></div>
<p class="abs copy">Copyrights 2013. All Rights Reserved.</p>
<div class="abs social">
  <span style="background:#3b5a9a"></span><span style="background:#555"></span><span style="background:#2aa3e0"></span><span style="background:#1f7bb6"></span>
</div>
</body>
</html>
```